Baseball Coaching Camp for 5-14year olds needs sales campaign

Local baseball coaching camp for children is in it's 22nd year running a 4-5 week series of summer camps. Each year we use email marketing beginning around December to sell our camps to the parents to sign up their children for one or more weeks. All information about the camps can be seen on our website at https://hemmingtarn.com/. In the past we have had success by changing the look of the emails each month and offering a decreasing discount as the camps get closer.

Our target market is the parents of children ages 5-14years old who like and play baseball and are interested in improving their skills in a fun environment during the Summer months.

We would like to improve the sales by developing new creative and imaginative emails for this season. We need 6 to 8 quality ads that can somehow relate to each other , these ads will be sent via our mailing list as well as used on social media. One of the owners thought it would be nice to use the "river of lanterns" theme though we are open to all ideas.
We have given you access to a dropbox link with examples of past campaigns along with artwork and images here
https://www.filequay.net/sh/q7ptr2mzk4wnhd/BBReo-kmTulf5pLXU318jw6Hb?dl=0

```html
<!DOCTYPE html>
<html lang="en">
<head>
<meta charset="utf-8">
<title>Hemmingtarn Baseball Academy</title>
<link rel="stylesheet" href="https://fonts.googleapis.com/css2?family=Raleway:wght@400;500;600;700;800&family=Fira+Sans:wght@400;500&display=swap">
<style>
:root{
  --blue:#4b58ad;
  --blue-deep:#3c47a0;
  --blue-light:#6470c4;
  --ink:#1b1b1b;
  --body:#333;
  --white:#fff;
  --black:#000;
  --green:#48b36b;
  --gold:#e8b21d;
}
*{margin:0;padding:0;box-sizing:border-box}
html,body{width:1200px;height:3874px;overflow:hidden;background:var(--white)}
body{position:relative;font-family:"Fira Sans",sans-serif;color:var(--body)}
.abs{position:absolute}
h1,h2,h3{font-family:"Raleway",sans-serif;font-weight:500;color:var(--ink)}

/* hero */
.hero{left:0;top:0;width:1200px;height:776px;
  background:linear-gradient(180deg,#7d8894 0%,#8d949c 20%,#5e7240 36%,#9a6f45 50%,#b47e4c 66%,#7c6a3e 84%,#55652f 100%)}
.hero-shade{left:0;top:0;width:1200px;height:776px;background:rgba(0,0,0,.22)}
.hero-logo{left:0;width:1200px;top:18px;text-align:center;font-family:"Raleway",sans-serif;font-weight:800;font-size:60px;color:var(--blue-deep);letter-spacing:2px}
.hero-title{left:0;top:200px;width:1200px;text-align:center;color:var(--white);font-size:78px;line-height:96px;font-weight:500;letter-spacing:1px}
.hero-text{left:168px;top:410px;width:864px;text-align:center;color:var(--white);font-size:20.5px;line-height:42px}
.social{display:flex;gap:20px}
.social span{display:block;width:48px;height:48px;border-radius:50%;background:var(--white)}
.hero-social{left:468px;top:575px}

/* text sections */
.section-title{left:0;width:1200px;text-align:center;font-size:36px;letter-spacing:.5px}
.section-text{left:94px;width:1012px;text-align:center;font-size:20.5px;line-height:42px}

/* photo trio */
.photo{top:1078px;width:400px;height:392px}
.band{left:0;top:1470px;width:1200px;height:98px;background:var(--blue);display:flex}
.band div{flex:1;color:var(--white);font-size:27px;display:flex;align-items:center;justify-content:center}

/* dates & pricing */
.team-photo{left:0;top:1905px;width:1200px;height:531px;
  background:linear-gradient(180deg,#2f4628 0%,#4a6436 35%,#5f6f8c 55%,#d2b23c 72%,#6f8a45 100%)}
.card{top:1993px;width:389px;height:357px;background:var(--white);text-align:center;padding-top:30px}
.card h3{font-size:27px;margin-bottom:14px}
.card p{font-size:19.5px;line-height:42px;color:#222}
.save{color:var(--blue)}

/* facilities */
.fac-title{left:112px;top:2602px;width:520px;text-align:center;font-size:36px}
.fac-text{left:108px;top:2660px;width:528px;text-align:center;font-size:20.5px;line-height:42px}
.fac-photo{left:680px;top:2512px;width:442px;height:481px;background:linear-gradient(180deg,#3d3f3d 0%,#5a5c58 35%,#c9a93a 50%,#8f8c82 70%,#c8b28a 100%)}

/* promo */
.promo{left:0;top:3080px;width:1200px;height:430px;background:linear-gradient(135deg,var(--blue-light) 0%,var(--blue) 55%,var(--blue-deep) 100%)}
.badge-art{left:38px;top:3062px;width:470px;height:420px;border-radius:40px;background:linear-gradient(135deg,#3a62a8 0%,#4fa56a 45%,#e8b21d 80%)}
.promo-seal{left:428px;top:3280px;width:196px;height:196px;border-radius:50%;background:var(--white);border:5px solid var(--green);text-align:center;color:#111;padding-top:26px}
.promo-seal .s1{font-size:22px}
.promo-seal .s2{font-size:42px;color:var(--blue);font-weight:500;line-height:48px}
.promo-seal .s3{font-size:15px}
.promo-seal .s4{font-size:23px}
.promo-copy{left:664px;top:3152px;width:500px;color:var(--white)}
.promo-copy h2{color:var(--white);font-size:36px;font-weight:500;margin-bottom:12px}
.promo-copy .sub{font-family:"Raleway",sans-serif;font-size:24px;margin-bottom:14px}
.promo-copy p{font-size:20px;line-height:31px;margin-bottom:26px}
.btn{display:inline-block;background:var(--white);color:var(--blue);font-size:21px;padding:12px 30px;border-radius:28px}

/* footer */
.footer{left:0;top:3510px;width:1200px;height:364px;background:var(--black)}
.footer-text,.footer-text h3{color:var(--white)}
.footer-text h3{font-size:26px;font-weight:600}
.contact{left:76px;top:3578px;width:300px}
.contact p{font-size:19px;line-height:32px;margin-top:14px}
.footer-logo{left:430px;top:3590px;width:340px;text-align:center;font-family:"Raleway",sans-serif;font-weight:800;font-size:120px}
.follow{right:76px;top:3578px;width:320px;text-align:right}
.follow .social{justify-content:flex-end;margin-top:20px}
.follow .links{font-size:19px;line-height:32px;margin-top:20px;text-align:left;margin-left:auto;width:302px}
.copyright{right:76px;top:3786px;font-size:19px}
</style>
</head>
<body>

<section class="abs hero" role="img" aria-label="Photo of a young batter at home plate on a sunlit baseball diamond"></section>
<div class="abs hero-shade"></div>
<div class="abs hero-logo">HT</div>
<h1 class="abs hero-title">HEMMINGTARN BASEBALL<br>ACADEMY</h1>
<p class="abs hero-text">This is the place to be if you are looking to give your child a baseball experience second to none! This camp is geared toward baseball players ages 5 to 14 who are looking to improve their skills and knowledge of the game.</p>
<div class="abs social hero-social" aria-label="Social links"><span></span><span></span><span></span><span></span></div>

<h2 class="abs section-title" style="top:838px">TRANSPORTATION &amp; LUNCH</h2>
<p class="abs section-text" style="top:902px">Transportation and lunch must be provided by the camper's parent or guardian. Lunch will be stored in coolers. If you prefer, we have contracted with an outside catering service to have lunch delivered each day. More information will be available when you register. Water will be provided throughout the day.</p>

<div class="abs photo" style="left:0;background:linear-gradient(180deg,#8a9a6a 0%,#6f7d45 30%,#c9a63a 60%,#4e5e34 100%)" role="img" aria-label="Photo of campers walking out of a cornfield"></div>
<div class="abs photo" style="left:400px;background:linear-gradient(180deg,#6f8a5a 0%,#8ea06e 20%,#b59a78 45%,#c9ab84 100%)" role="img" aria-label="Photo of a young camper swinging a bat"></div>
<div class="abs photo" style="left:800px;background:linear-gradient(180deg,#6a9a4a 0%,#4a70b8 25%,#d8b82a 60%,#e3c22a 100%)" role="img" aria-label="Photo of two young campers in caps"></div>
<div class="abs band"><div>Each Camper Should Bring</div><div>Special Clinics</div><div>Each Camper Will Receive</div></div>

<h2 class="abs section-title" style="top:1632px">CAMP OBJECTIVES</h2>
<p class="abs section-text" style="top:1696px">HEMMINGTARN BASEBALL CAMP provides a safe, fun, and educational environment where both beginner, as well as experienced players can excel. Throughout the week, your child will learn the basic fundamentals of the game and be able to specialize in the position of their choice. Each camper will learn the importance of team work, sportsmanship, and fair play.</p>

<div class="abs team-photo" role="img" aria-label="Group photo of campers and coaches on a field"></div>
<div class="abs card" style="left:143px">
  <h3>2022 CAMP DATES</h3>
  <p>WEEK 1: June 27 - July 1<br>@Ashcombe Park - Fernmoor<br>WEEK 2: July 11 - July 15 @Tallis<br>Park-Oakrill<br>WEEK 3: July 18 - July 22<br>@Ashcombe Road Park - Fernmoor</p>
</div>
<div class="abs card" style="left:667px">
  <h3>2022 PRICING</h3>
  <p>Half Day (5 year olds only) - $225<br>Full Day 1 Week - $350<br>Full Day 2 Week - $650 - <span class="save">Save $50</span><br>Full Day 3 Week - $925 - <span class="save">Save $125</span><br>Full Day 4 Week - $1,125 -<br>Save <span class="save">$275</span></p>
</div>

<h2 class="abs fac-title">OUR FACILITIES</h2>
<p class="abs fac-text">Lorem ipsum dolor sit amet, consectetur adipiscing elit, sed do eiusmod tempor incididunt ut labore et dolore magna aliqua. Quis ipsum suspendisse ultrices gravida. Risus commodo viverra maecenas accumsan lacus vel facilisis. Lorem ipsum dolor sit amet, consectetur adipiscing elit, sed do eiusmod</p>
<div class="abs fac-photo" role="img" aria-label="Photo of a camper in a batting helmet ready to hit"></div>

<section class="abs promo"></section>
<div class="abs badge-art" role="img" aria-label="Illustrated 22 years anniversary celebration emblem"></div>
<div class="abs promo-seal">
  <div class="s1">SAVE MONEY</div>
  <div class="s2">$5 OFF</div>
  <div class="s3">PROMO CODE</div>
  <div class="s4">PLAY BALL</div>
</div>
<div class="abs promo-copy">
  <h2>LEARN TO PLAY LIKE A PRO</h2>
  <div class="sub">Sign Up Today And Save Money</div>
  <p>Lorem ipsum dolor sit amet, consectetur adipiscing elit, sed do eiusmod tempor incididunt</p>
  <span class="btn">Sign Up</span>
</div>

<footer class="abs footer"></footer>
<div class="abs contact footer-text">
  <h3>CONTACT US</h3>
  <p>Lorem ipsum dolor sit amet, consectetur adipiscing</p>
  <p>188-888-888</p>
  <p>info@companyname.com</p>
</div>
<div class="abs footer-logo footer-text">HT</div>
<div class="abs follow footer-text">
  <h3>FOLLOW US ON</h3>
  <div class="social"><span></span><span></span><span></span><span></span></div>
  <div class="links">Terms&amp;condtions Privacy Policy<br>About Us Support</div>
</div>
<div class="abs copyright footer-text">©Copyrights 2021 Company Name &nbsp;| &nbsp;&nbsp;All Rights Reserved</div>

</body>
</html>
```